Barrister at Law needs Business Card Design

Need a business card design for Barrister at Law. Double sided. Simple Neil Thorsby and Barrister at Law on one side with contact details on the other side. I would like a professional design using Black or Platinum. Details on reverse side would include qualifications - Bcom-Llb and Acc Spec Commercial Litigation. I have attached the logo. Contact details would include address/ Po Box/ Phone/Fax/Mobile/email. I would like to use raised print or spot gloss.

```html
<!DOCTYPE html>
<html lang="en">
<head>
<meta charset="utf-8">
<title>Neil Thorsby – Barrister at Law Business Card</title>
<link rel="stylesheet" href="https://fonts.googleapis.com/css2?family=Cinzel:wght@400;600&family=Open+Sans:wght@400;600;700&display=swap">
<style>
  :root {
    --backdrop: #2f2925;
    --card-black-top: #454545;
    --card-black-bottom: #000000;
    --platinum-light: #f2f2f2;
    --platinum-mid: #a9a9a9;
    --platinum-dark: #6d6d6d;
    --card-blue: #0b7fd0;
    --blue-mark: #1a8ddc;
    --ink-white: #ffffff;
    --ink-soft: #d6ebfb;
  }
  * { margin: 0; padding: 0; box-sizing: border-box; }
  html, body {
    width: 1200px; height: 844px; overflow: hidden;
    background: var(--backdrop);
  }
  .canvas {
    position: relative; width: 1200px; height: 844px;
    display: flex; align-items: center; justify-content: center; gap: 60px;
  }
  .card {
    position: relative; width: 520px; height: 298px;
    border-radius: 3px;
    box-shadow: 0 14px 30px rgba(0,0,0,.45);
    overflow: hidden;
  }
  /* Front */
  .card-front {
    background: linear-gradient(180deg, var(--card-black-top) 0%, #151515 45%, var(--card-black-bottom) 100%);
    display: flex; flex-direction: column; justify-content: center; align-items: center;
  }
  .front-title {
    font-family: "Cinzel", serif; font-weight: 400;
    font-size: 44px; line-height: 1.22; letter-spacing: 1px;
    text-align: center;
    background: linear-gradient(180deg, var(--platinum-light) 0%, var(--platinum-mid) 55%, var(--platinum-dark) 100%);
    -webkit-background-clip: text; background-clip: text; color: transparent;
    filter: drop-shadow(0 2px 1px rgba(0,0,0,.9));
  }
  /* Back */
  .card-back {
    background: var(--card-blue);
    font-family: "Open Sans", sans-serif; color: var(--ink-white);
    padding: 70px 0 0 66px;
  }
  .brand-mark {
    position: absolute; top: 58px; right: 34px;
    font-family: "Open Sans", sans-serif; font-weight: 700;
    font-size: 34px; color: var(--blue-mark); letter-spacing: .5px;
  }
  .holder-name { font-weight: 700; font-size: 17px; line-height: 1.1; }
  .holder-name .qualifications { font-size: 11px; font-weight: 600; }
  .specialty { font-size: 12px; color: var(--ink-soft); margin-top: 2px; }
  .address { font-size: 12px; color: var(--ink-soft); line-height: 1.3; margin-top: 24px; }
  .contact-list { list-style: none; margin-top: 22px; margin-left: 30px; }
  .contact-list li {
    display: flex; align-items: center; gap: 8px;
    font-size: 12.5px; line-height: 17px;
  }
  .contact-list svg { width: 10px; height: 10px; fill: var(--ink-white); flex: none; }
  .contact-list .icon-link { fill: none; stroke: var(--ink-white); stroke-width: 1.4; }
</style>
</head>
<body>
<main class="canvas">
  <section class="card card-front" aria-label="Card front">
    <h1 class="front-title">Neil Thorsby<br>Barrister at Law</h1>
  </section>

  <section class="card card-back" aria-label="Card back">
    <div class="brand-mark">Thorsby Law</div>
    <p class="holder-name">Neil Thorsby <span class="qualifications">Bcom, LLB</span></p>
    <p class="specialty">Acc Spec Commercial Litigation</p>
    <p class="address">12345, Address Goes Here<br>Country Name, 123456</p>
    <ul class="contact-list">
      <li>
        <svg viewBox="0 0 10 10" aria-hidden="true"><path d="M1 3c0-1 1-2 4-2s4 1 4 2l-2 .6-.4-1H3.4L3 3.6zM2.5 5h5L9 9H1z"/></svg>
        (044)-555-0142
      </li>
      <li>
        <svg viewBox="0 0 10 10" aria-hidden="true"><path d="M3 0h4v3H3zM1 3.5h8V9H1zM3 5v1h4V5z"/></svg>
        123-555-0187
      </li>
      <li>
        <svg viewBox="0 0 10 10" aria-hidden="true"><path d="M0 2h10v6H0zM1 2.8v.6l4 2.6 4-2.6v-.6L5 5.2z"/></svg>
        info@thorsbylaw.example
      </li>
      <li>
        <svg class="icon-link" viewBox="0 0 10 10" aria-hidden="true"><path d="M4.2 5.8 2.6 7.4a1.3 1.3 0 0 1-1.9-1.9L2.4 3.8M5.8 4.2l1.6-1.6a1.3 1.3 0 0 0-1.9-1.9L3.8 2.4M3.6 6.4l2.8-2.8"/></svg>
        www.thorsbylaw.example
      </li>
    </ul>
  </section>
</main>
</body>
</html>
```